Computer consultant business card

Bexil Software is a newly started computer consulting company. It's a small one-man company that provides mostly Vornix applications but also websites in collaboration with designers. I'm running this company on the side of full time university studies.

I want the final design to be clean and memorable. Be creative! :)

Some inspiration:
http://www.pixelmarta.com/design/48317
http://www.pixelmarta.com/design/2739164/business-card-design-by-frostlynk
http://www.pixelmarta.com/design/604281/business-card-design-by-koralind-vestrabanu

See attachment for my company logo.
Updates

I would like to thank everyone for submitting! I'll need a couple of days to review and ultimately select a design.

Target Market(s)

Non-technical entrepreneurs and small companies.

Industry/Entity Type

University

Requirements
Must have
• My company logo.
In any way, both colors from my logo.
First- and last name, e-mail and phone number.
Double-sided design.
Nice to have
• Something creative with the symbol in my logo

```html
<!DOCTYPE html>
<html lang="en">
<head>
<meta charset="utf-8">
<title>Qyndo Software – Business Card</title>
<link href="https://fonts.googleapis.com/css2?family=Comfortaa:wght@700&family=Arimo:wght@400&family=Tinos&display=swap" rel="stylesheet">
<style>
  :root {
    --page-bg: #e9e9ea;
    --blue-light: #79a6d6;
    --blue-mid: #4c7fbc;
    --blue-dark: #2b5792;
    --logo-grey: #4a4a4c;
    --title-grey: #5a5a5c;
    --text-grey: #4d4d4f;
    --accent-blue: #5b8fcf;
    --card-white: #fbfbfb;
  }
  * { box-sizing: border-box; margin: 0; padding: 0; }
  html, body {
    width: 1200px;
    height: 900px;
    overflow: hidden;
    background: var(--page-bg);
  }
  .canvas {
    width: 1200px;
    height: 900px;
    display: flex;
    flex-direction: column;
    align-items: center;
    justify-content: center;
    gap: 44px;
  }
  .card {
    position: relative;
    width: 640px;
    height: 366px;
    box-shadow: 0 10px 28px rgba(0,0,0,.18);
    overflow: hidden;
  }
  /* Front side */
  .card-front {
    display: flex;
    align-items: center;
    justify-content: center;
    background: radial-gradient(ellipse at 50% 52%, var(--blue-light) 0%, var(--blue-mid) 48%, var(--blue-dark) 100%);
  }
  .front-brand {
    display: flex;
    align-items: center;
    gap: 30px;
  }
  .brand-mark {
    flex: none;
    width: 104px;
    height: 104px;
    border-radius: 50%;
    background: var(--logo-grey);
  }
  .brand-name {
    font-family: "Comfortaa", sans-serif;
    font-weight: 700;
    color: var(--logo-grey);
    letter-spacing: 1px;
    line-height: 1;
    white-space: nowrap;
  }
  .front-brand .brand-name { font-size: 78px; }
  /* Back side */
  .card-back { background: var(--card-white); }
  .contact-list {
    position: absolute;
    right: 40px;
    top: 40px;
    list-style: none;
    font-family: "Arimo", sans-serif;
    font-size: 13px;
    color: var(--text-grey);
  }
  .contact-item {
    display: flex;
    align-items: center;
    gap: 10px;
    height: 19px;
  }
  .contact-icon { width: 11px; height: 11px; fill: var(--accent-blue); flex: none; }
  .back-brand {
    position: absolute;
    left: 44px;
    bottom: 54px;
    display: flex;
    align-items: center;
    gap: 20px;
  }
  .back-brand .brand-mark {
    width: 84px;
    height: 84px;
    background: var(--accent-blue);
  }
  .back-brand .brand-name { font-size: 54px; }
  .brand-stack {
    display: flex;
    flex-direction: column;
    gap: 6px;
  }
  .job-title {
    font-family: "Tinos", serif;
    font-size: 20px;
    letter-spacing: 3px;
    line-height: 1.05;
    color: var(--title-grey);
    text-transform: uppercase;
  }
</style>
</head>
<body>
  <main class="canvas">
    <section class="card card-front" aria-label="Card front">
      <div class="front-brand">
        <span class="brand-mark" aria-hidden="true"></span>
        <span class="brand-name">qyndo</span>
      </div>
    </section>

    <section class="card card-back" aria-label="Card back">
      <ul class="contact-list">
        <li class="contact-item">
          <svg class="contact-icon" viewBox="0 0 12 12"><path d="M3 1 L5 3.4 L3.8 4.8 C4.5 6.3 5.7 7.5 7.2 8.2 L8.6 7 L11 9 L9.6 11 C5 10.6 1.4 7 1 2.4 Z"/></svg>
          <span>+(000) 1234 5678</span>
        </li>
        <li class="contact-item">
          <svg class="contact-icon" viewBox="0 0 12 12"><rect x="1" y="1" width="10" height="2"/><rect x="1" y="5" width="10" height="2"/><rect x="1" y="9" width="10" height="2"/></svg>
          <span>+(000) 1234 5679</span>
        </li>
        <li class="contact-item">
          <svg class="contact-icon" viewBox="0 0 12 12"><path d="M1 2.5 H11 V9.5 H1 Z M1.8 3.2 L6 6.4 L10.2 3.2" fill="none" stroke="var(--accent-blue)" stroke-width="1.2"/></svg>
          <span>email@yourdomain.com</span>
        </li>
        <li class="contact-item">
          <svg class="contact-icon" viewBox="0 0 12 12"><circle cx="6" cy="6" r="5"/></svg>
          <span>www.yourwebsite.com</span>
        </li>
      </ul>

      <div class="back-brand">
        <span class="brand-mark" aria-hidden="true"></span>
        <div class="brand-stack">
          <span class="brand-name">qyndo</span>
          <p class="job-title">Managing<br>Director</p>
        </div>
      </div>
    </section>
  </main>
</body>
</html>
```